NZ First of it's kind solutions directory and marketplace for busy Mums needs a business card design

We need a business card design for our new nationwide business in NZ (long term plans to go global). We provide solutions to the everyday challenges that busy Mums face by connecting them with quality communities and suppliers of carefully selected, relevant products and services. We sell direct via our online marketplace. The final design should communicate our values of inclusivity, quality and smart solutions. Colours should incorporate our logo colour palette of #477077 and #6ba8b2. Our website is at https://www.brightnestmums.example

Target Market(s)

busy Mums, Age 28 – 50, female, income over $100K, location main centres NZ primarily but NZ wide. Is likely juggling work or career with a young family. Probably had hobbies which have fallen by the wayside.
-Wants to succeed in her chosen career without compromising on family life
-to successfully juggle her career without feeling like she is compromising her children
- Is time poor, something always has to give and it’s generally her health (she’ll stay up late, get stressed)
- probably ex corporate or professional career. Has discretional income

Industry/Entity Type

Business

Contact Information for Business Card

Lena Forbisher, Founder, BrightNestMums.example (Strapline Tap; Gather; Sorted), 47 Kowhai Terrace, Ellerslie, Auckland 1051, New Zealand. Mob: 021 483 517 Ph: +64 (0)9 571 4860

Font styles to use
Other font styles liked:
• Raleway, and/or Architects Daughter

Colors
00a990
33b8a4
86cfc6
cfeae6

Requirements
Must have
• the above details, streamline. the logo and colours associated with those logos
Should not have
• foil or metallic colours

```html
<!DOCTYPE html>
<html lang="en">
<head>
<meta charset="utf-8">
<title>BrightNestMums – Business Card</title>
<link rel="stylesheet" href="https://fonts.googleapis.com/css2?family=Roboto:wght@400;500;700&family=Roboto+Condensed:wght@700&display=swap">
<style>
  :root {
    --teal-dark: #477077;
    --teal-light: #6ba8b2;
    --paper: #f2f2f2;
    --white: #ffffff;
    --backdrop: #2a2a2a;
  }
  * { margin: 0; padding: 0; box-sizing: border-box; }
  html, body { width: 1200px; height: 960px; overflow: hidden; }
  body {
    background: var(--backdrop);
    font-family: "Roboto", Arial, sans-serif;
    position: relative;
  }
  .card {
    position: absolute;
    width: 600px;
    height: 343px;
    overflow: hidden;
    box-shadow: 2px 3px 6px rgba(0,0,0,0.5);
  }
  .card--front { left: 314px; top: 113px; background: var(--paper); }
  .card--back { left: 311px; top: 472px; background: var(--teal-light); }

  .wave { position: absolute; inset: 0; }

  .brand {
    position: absolute;
    left: 44px;
    top: 155px;
    display: flex;
    align-items: center;
    gap: 10px;
  }
  .brand__dot {
    width: 24px; height: 24px; border-radius: 50%;
    background: var(--teal-dark);
  }
  .brand__name {
    font-weight: 700;
    font-size: 27px;
    color: var(--teal-dark);
    letter-spacing: -0.3px;
  }

  .contact {
    position: absolute;
    right: 25px;
    top: 76px;
    text-align: right;
    color: var(--white);
  }
  .contact__name {
    font-family: "Roboto Condensed", "Arial Narrow", sans-serif;
    font-weight: 700;
    font-size: 22px;
    line-height: 26px;
    letter-spacing: 0.2px;
  }
  .contact__title { font-size: 15px; line-height: 20px; font-weight: 500; }
  .contact__address { margin-top: 12px; font-size: 14.5px; line-height: 18px; }
  .contact__lines { margin-top: 13px; font-size: 14.5px; line-height: 19.5px; }
  .contact__line { display: flex; justify-content: flex-end; align-items: center; gap: 6px; }
  .contact__icon { width: 13px; height: 13px; fill: var(--white); }

  .back-brand {
    position: absolute;
    left: 0; right: 0; top: 120px;
    display: flex;
    flex-direction: column;
    align-items: center;
    gap: 16px;
  }
  .back-brand__dot { width: 40px; height: 40px; border-radius: 50%; background: var(--white); }
  .back-brand__name { font-weight: 700; font-size: 34px; color: var(--white); }
  .strapline {
    position: absolute;
    left: 0; right: 0; top: 304px;
    text-align: center;
    font-size: 14.5px;
    color: var(--white);
  }
</style>
</head>
<body>

<section class="card card--front">
  <svg class="wave" viewBox="0 0 600 343" width="600" height="343" aria-hidden="true">
    <path d="M350,0 C322,60 322,130 332,190 C345,260 345,300 315,343 L342,343 C360,300 355,250 345,190 C335,130 330,60 355,0 Z" fill="var(--teal-light)"/>
    <path d="M355,0 C330,60 335,130 345,190 C355,250 360,300 342,343 L600,343 L600,0 Z" fill="var(--teal-dark)"/>
    <path d="M350,0 C322,60 322,130 332,190 C345,260 345,300 315,343" fill="none" stroke="var(--white)" stroke-width="1.5"/>
  </svg>

  <div class="brand">
    <span class="brand__dot"></span>
    <span class="brand__name">BrightNestMums</span>
  </div>

  <div class="contact">
    <div class="contact__name">LENA FORBISHER</div>
    <div class="contact__title">FOUNDER</div>
    <div class="contact__address">
      47 Kowhai Terrace<br>
      Ellerslie, Auckland<br>
      1051, New Zealand
    </div>
    <div class="contact__lines">
      <div class="contact__line">+64 (0)9 571 4860
        <svg class="contact__icon" viewBox="0 0 24 24"><path d="M6.6 10.8a15.1 15.1 0 0 0 6.6 6.6l2.2-2.2a1 1 0 0 1 1-.25 11.4 11.4 0 0 0 3.6.57 1 1 0 0 1 1 1V20a1 1 0 0 1-1 1A17 17 0 0 1 3 4a1 1 0 0 1 1-1h3.5a1 1 0 0 1 1 1 11.4 11.4 0 0 0 .57 3.6 1 1 0 0 1-.25 1z"/></svg>
      </div>
      <div class="contact__line">021 483 517
        <svg class="contact__icon" viewBox="0 0 24 24"><path d="M7 1h10a2 2 0 0 1 2 2v18a2 2 0 0 1-2 2H7a2 2 0 0 1-2-2V3a2 2 0 0 1 2-2zm0 3v14h10V4zm5 15.5a1.2 1.2 0 1 0 0 2.4 1.2 1.2 0 0 0 0-2.4z"/></svg>
      </div>
      <div class="contact__line">BrightNestMums.example
        <svg class="contact__icon" viewBox="0 0 24 24"><circle cx="12" cy="12" r="11"/><path d="M7 6c2 1 3 3 2 5s-3 1-3 4l2 3M15 4c-1 2 1 3 3 4s1 4-1 5-1 4 0 6" stroke="var(--teal-dark)" stroke-width="2" fill="none"/></svg>
      </div>
    </div>
  </div>
</section>

<section class="card card--back">
  <div class="back-brand">
    <span class="back-brand__dot"></span>
    <span class="back-brand__name">BrightNestMums</span>
  </div>
  <p class="strapline">Tap; Gather; Sorted</p>
</section>

</body>
</html>
```